Website Design Project for Beauty & Wellness Professionals

As background information, I have a website that is focused on Beauty & Wellness Professionals:
- Job Search (www.lumarinovo.com)
- Business Classifieds (negocios.lumarinovo.com)
- Freelancer Classifieds (freelancer.lumarinovo.com)
- Course Reviews (cursos.lumarinovo.com)

All those websites use standard templates.

I need a DESIGN for the HOME PAGE (no coding) of the Website Platform that consolidates the four platforms under the same design.

Website designs that we like:
- quelvox.com
- brintmoor.com

Target Market(s)

Brazilian Professionals from Beauty & Wellness sector

Industry/Entity Type

Business

Requirements
Must have
• Website designs that we like:
- quelvox.com
- brintmoor.com

```html
<!DOCTYPE html>
<html lang="en">
<head>
<meta charset="utf-8">
<title>Lumarinovo Beauty – Home</title>
<link href="https://fonts.googleapis.com/css2?family=Roboto+Condensed:wght@400;700&family=Roboto:wght@400;500;700&display=swap" rel="stylesheet">
<style>
:root{
  --dark:#2f2f2f;
  --orange:#e8561f;
  --red:#d8261f;
  --green:#3fa629;
  --lime:#8cc63e;
  --purple:#9b59b6;
  --grey:#6e6e6e;
  --teal:#3ea3b4;
  --text:#555;
  --line:#e3e3e3;
  --blue:#1b8fd0;
}
*{box-sizing:border-box;margin:0;padding:0}
html,body{width:832px;height:1200px;overflow:hidden}
body{position:relative;background:#fff;font-family:Roboto,Arial,sans-serif;color:var(--text)}
.abs{position:absolute}
.cond{font-family:"Roboto Condensed",Arial,sans-serif}

.top-nav{left:0;top:0;width:832px;height:20px;background:var(--dark)}
.top-nav a{position:absolute;top:5px;font:400 10px "Roboto Condensed",sans-serif;color:#ccc;text-decoration:none;letter-spacing:.2px}
.top-nav a.active{color:var(--orange)}

.header{left:0;top:20px;width:832px;height:90px;background:linear-gradient(#fafafa,#e9e9e9);border-bottom:1px solid #cfcfcf}
.brand{left:83px;display:flex;align-items:center;gap:6px}
.brand-dot{width:14px;height:14px;border-radius:50%;background:var(--teal)}
.brand-name{font:400 19px "Roboto Condensed",sans-serif;color:var(--teal)}
.btn{position:absolute;display:flex;align-items:center;justify-content:center;color:#fff;font:700 10px "Roboto Condensed",sans-serif;letter-spacing:.4px;border-radius:1px}
.btn-green{background:var(--green)}
.btn-orange{background:var(--orange)}

.hero{left:0;top:110px;width:832px;height:253px;background:linear-gradient(100deg,#c8d2dc 0%,#7e8ea0 30%,#3a5577 55%,#8a97a6 80%,#c4c9cf 100%)}
.hero-title{left:0;width:832px;top:50px;text-align:center;font:700 26px "Roboto Condensed",sans-serif;color:var(--orange);letter-spacing:.6px}
.search{left:90px;top:104px;width:652px;height:39px;background:#1e1e1e;border-radius:2px}
.field{position:absolute;top:5px;height:29px;background:#fff;font:400 11px Roboto,sans-serif;color:#666;display:flex;align-items:center;padding-left:9px;letter-spacing:.3px}
.search-btn{position:absolute;left:562px;top:5px;width:86px;height:29px;background:#3ea6c7;color:#fff;font:500 13px "Roboto Condensed",sans-serif;display:flex;align-items:center;justify-content:center;letter-spacing:.6px}
.hero-hint{left:0;width:832px;top:164px;text-align:center;font:700 12px "Roboto Condensed",sans-serif;color:#fff}
.dots{left:404px;top:227px;display:flex;gap:3px}
.dots span{width:5px;height:5px;border-radius:50%;background:#ccc}
.dots span:first-child{background:#333}

.section-title{font:700 15px "Roboto Condensed",sans-serif;color:#333;letter-spacing:.4px}
.tab{position:absolute;top:407px;height:19px;color:#fff;font:400 10px Roboto,sans-serif;display:flex;align-items:center;justify-content:center;letter-spacing:.3px}

.job{position:absolute;left:83px;width:437px;height:68px;border:1px solid var(--line);background:#fff}
.date{position:absolute;left:7px;top:7px;width:56px;height:55px;color:#fff;text-align:center;font-family:"Roboto Condensed",sans-serif}
.date .m{font-size:8px;margin-top:7px}
.date .d{font:700 21px/20px "Roboto Condensed",sans-serif}
.date .y{font-size:8px}
.job-body{position:absolute;left:82px;top:8px;width:222px;display:flex;flex-direction:column;gap:6px}
.job-title{font:400 11px/13px Roboto,sans-serif;color:var(--red);text-align:justify}
.job-meta{font:400 7.5px/10px Roboto,sans-serif;color:#666}
.job-meta b{font-weight:400;color:var(--red)}
.job-place{position:absolute;left:315px;top:6px;bottom:6px;border-left:1px solid var(--line);padding-left:11px;width:116px}
.job-place .city{font:400 11px Roboto,sans-serif;color:var(--orange);margin-top:6px}
.job-place .state{font:400 8px/10px Roboto,sans-serif;color:#777;margin-top:5px}

.page{position:absolute;top:745px;height:20px;border:1px solid #ddd;border-radius:2px;background:#fafafa;font:500 9px Roboto,sans-serif;color:#444;display:flex;align-items:center;justify-content:center}

.course{position:absolute;top:816px;width:208px;height:200px;border:1px solid var(--line);background:#fff}
.course-img{position:absolute;left:10px;top:12px;width:184px;height:108px}
.course-cap{position:absolute;left:0;bottom:0;width:100%;height:20px;background:rgba(0,0,0,.75);color:#fff;font:400 10px "Roboto Condensed",sans-serif;padding:4px 8px}
.course-text{position:absolute;left:20px;top:128px;width:168px;font:400 7px/9px Roboto,sans-serif;color:#222}
.course-text em{font-style:normal;color:var(--orange)}
.course-btn{position:absolute;left:20px;top:168px;width:96px;height:18px;background:var(--orange);color:#fff;font:700 7px Roboto,sans-serif;display:flex;align-items:center;justify-content:center}
.course-brand{position:absolute;right:22px;top:170px;display:flex;align-items:center;gap:3px;font:700 11px Roboto,sans-serif;color:#444}
.course-brand i{width:11px;height:11px;background:var(--orange);display:block}

.box{position:absolute;left:541px;width:207px;border:1px solid var(--line);background:#fff}
.big-btn{position:absolute;left:7px;width:193px;color:#fff;font:700 15px "Roboto Condensed",sans-serif;display:flex;align-items:center;justify-content:center;letter-spacing:.8px}
.cats{position:absolute;left:0;top:32px;width:100%;list-style:none}
.cats li{height:20.8px;border-top:1px solid #eee;font:400 8.5px Roboto,sans-serif;color:#333;display:flex;align-items:center;padding-left:27px;position:relative;letter-spacing:.2px}
.cats li::before{content:"";position:absolute;left:11px;top:7px;border-left:4px solid var(--red);border-top:3px solid transparent;border-bottom:3px solid transparent}
.social{display:flex;gap:5px}
.social span{width:16px;height:16px;border-radius:3px;display:block}

.promo{left:162px;top:1033px;width:505px;height:63px;background:#f39c1f;overflow:hidden}
.promo-side{position:absolute;right:0;top:0;width:122px;height:63px;background:var(--blue)}

.footer{left:0;top:1112px;width:832px;height:61px;background:#3a3a3a;text-align:center;font:400 9px/16.5px "Roboto Condensed",sans-serif;color:#bbb;padding-top:6px}
.footer b{font-weight:400;color:var(--orange)}
.copy{left:0;top:1173px;width:832px;height:27px;background:#2a2a2a;text-align:center;font:400 7.5px/27px "Roboto Condensed",sans-serif;color:#999}
</style>
</head>
<body>

<nav class="abs top-nav">
  <a class="active" style="left:98px">HOME</a>
  <a style="left:163px">BLOG</a>
  <a style="left:229px">FOR PROFESSIONALS</a>
  <a style="left:357px">FOR BUSINESS</a>
  <a style="left:462px">EVENTS &amp; PARTNERS</a>
  <a style="left:592px">ABOUT U.S</a>
  <a style="left:678px">CONTACT US</a>
</nav>

<header class="abs header">
  <div class="abs brand" style="top:44px"><span class="brand-dot"></span><span class="brand-name">Lumarinovo Beauty</span></div>
  <span class="btn btn-green" style="left:499px;top:35px;width:140px;height:18px">ADVERTISE JOB VACANCY</span>
  <span class="btn btn-orange" style="left:645px;top:35px;width:45px;height:18px">LOGIN</span>
  <span class="btn btn-green" style="left:697px;top:35px;width:48px;height:18px">SIGN UP</span>
</header>

<section class="abs hero" role="img" aria-label="Blurred photo of a beauty salon scene with a red hat in the foreground">
  <div class="abs hero-title">LOCAL JOB SEARCH AND DESIRED!</div>
  <div class="abs search">
    <div class="field" style="left:6px;width:89px">JOBS
      <svg style="position:absolute;right:9px;top:12px" width="7" height="5"><path d="M0 0h7L3.5 5z" fill="#777"/></svg>
    </div>
    <div class="field" style="left:103px;width:228px">KEYWORDS</div>
    <div class="field" style="left:339px;width:215px">LOCATION</div>
    <div class="search-btn">SEARCH</div>
  </div>
  <div class="abs hero-hint">EX: MANICURE SÃO PAULO, RIO DE JANEIRO HAIRDRESSER</div>
  <div class="abs dots"><span></span><span></span><span></span></div>
</section>

<h2 class="abs section-title" style="left:83px;top:377px">FEATURED JOB VACANCIES</h2>
<span class="tab" style="left:83px;width:107px;background:var(--red)">REGISTERED (CLT)</span>
<span class="tab" style="left:197px;width:84px;background:var(--lime)">AUTONOMOUS</span>
<span class="tab" style="left:287px;width:78px;background:var(--purple)">TEMPORARY</span>
<span class="tab" style="left:371px;width:79px;background:var(--grey)">TEMPORARY</span>

<article class="job" style="top:441px">
  <div class="date" style="background:var(--red)"><div class="m">JULY</div><div class="d">18</div><div class="y">2013</div></div>
  <div class="job-body">
    <div class="job-title">Aux. Hairdresser (Escovista) - Santo André (SP)</div>
    <div class="job-meta">Marina Souza / Opala Hair and Esthetics - Posted by <b>Marina Souza</b></div>
  </div>
  <div class="job-place"><div class="city">Santo André</div><div class="state">São Paulo, the Federative Republic of Brazil</div></div>
</article>
<article class="job" style="top:517px">
  <div class="date" style="background:var(--purple)"><div class="m">JULY</div><div class="d">18</div><div class="y">2013</div></div>
  <div class="job-body">
    <div class="job-title">MANICURE - NEXT TO PQ SAO SUNDAYS - SP Espaço Lírio Estética Man</div>
    <div class="job-meta">Marina Souza / Opala Hair and Esthetics - Posted by <b>Marina Souza</b></div>
  </div>
  <div class="job-place"><div class="city">Santo André</div><div class="state">São Paulo, the Federative Republic of Brazil</div></div>
</article>
<article class="job" style="top:593px">
  <div class="date" style="background:var(--lime)"><div class="m">JULY</div><div class="d">18</div><div class="y">2013</div></div>
  <div class="job-body">
    <div class="job-title">Aux. Hairdresser (Escovista) - Santo André (SP)</div>
    <div class="job-meta">Marina Souza / Opala Hair and Esthetics - Posted by <b>Marina Souza</b></div>
  </div>
  <div class="job-place"><div class="city">Santo André</div><div class="state">São Paulo, the Federative Republic of Brazil</div></div>
</article>
<article class="job" style="top:669px">
  <div class="date" style="background:var(--lime)"><div class="m">JULY</div><div class="d">18</div><div class="y">2013</div></div>
  <div class="job-body">
    <div class="job-title">Aux. Hairdresser (Escovista) - Santo André (SP)</div>
    <div class="job-meta">Marina Souza / Opala Hair and Esthetics - Posted by <b>Marina Souza</b></div>
  </div>
  <div class="job-place"><div class="city">Santo André</div><div class="state">São Paulo, the Federative Republic of Brazil</div></div>
</article>

<span class="page" style="left:206px;width:38px">Prev</span>
<span class="page" style="left:254px;width:20px">1</span>
<span class="page" style="left:282px;width:20px">2</span>
<span class="page" style="left:310px;width:20px">3</span>
<span class="page" style="left:337px;width:20px">4</span>
<span class="page" style="left:365px;width:20px">5</span>
<span class="page" style="left:392px;width:20px">6</span>
<span class="page" style="left:420px;width:20px">...</span>
<span class="page" style="left:448px;width:20px">22</span>
<span class="page" style="left:476px;width:42px">Next</span>

<h2 class="abs section-title" style="left:83px;top:786px">ONLINE COURSES APRENDO</h2>
<article class="course" style="left:83px">
  <div class="course-img" role="img" aria-label="Photo of a makeup brush in pink powder" style="background:linear-gradient(135deg,#6a4a66,#b38aa8 50%,#5d4057)">
    <div class="course-cap">Curso de Maquiagem Profissional</div>
  </div>
  <p class="course-text">Seja um profissional mais qualificado, invista na sua carreira e se prepare para o mercado de trabalho. Matricule-se agora no curso Aprendo de <em>Maquiagem Profissional.</em></p>
  <span class="course-btn">EXPERIMENTE GRÁTIS</span>
  <span class="course-brand">aprendo<i></i></span>
</article>
<article class="course" style="left:311px">
  <div class="course-img" role="img" aria-label="Photo of a hairdresser cutting hair" style="background:linear-gradient(135deg,#d8d0c6,#a48a6c 45%,#e6e0da)">
    <div class="course-cap">Curso de Cabeleireiro Profissional</div>
  </div>
  <p class="course-text">Seja um profissional mais qualificado, invista na sua carreira e se prepare para o mercado de trabalho. Matricule-se agora no curso Aprendo de <em>Cabeleireiro Profissional.</em></p>
  <span class="course-btn">EXPERIMENTE GRÁTIS</span>
  <span class="course-brand">aprendo<i></i></span>
</article>

<aside>
  <div class="box" style="top:373px;height:69px">
    <span class="big-btn" style="top:7px;height:35px;background:var(--red)">ADVERTISE JOB VACANCY</span>
    <div class="abs cond" style="left:0;width:100%;top:50px;text-align:center;font-size:9px;font-weight:700;color:#444">ADVERTISE A VACANCY FREE!</div>
  </div>

  <div class="box" style="top:449px;height:387px">
    <h3 class="abs section-title" style="left:9px;top:7px;font-size:13px">JOB VACANCIES</h3>
    <ul class="cats">
      <li>Assistant Hairdresser</li><li>Assistant Cleaning</li><li>Hairdresser</li><li>Epilator</li>
      <li>Designer Eyebrow</li><li>Featured</li><li>Nurse</li><li>Beautician</li>
      <li>Physiotherapist</li><li>Management / Coordination</li><li>Manicure and Pedicure</li>
      <li>Makeup artist</li><li>Massage therapist</li><li>Other</li><li>Podiatrist</li>
      <li>Reception / Customer</li><li>Cosmetics sales</li>
    </ul>
  </div>

  <div class="box" style="top:844px;height:171px">
    <span class="big-btn" style="top:7px;height:35px;background:var(--orange)">SUBSCRIBE BY EMAIL</span>
    <p class="abs" style="left:11px;top:50px;width:188px;font-size:7px;line-height:9px;color:#666">Enter your email address to subscribe and receive notifications of new posts by email.</p>
    <div class="abs" style="left:7px;top:76px;width:193px;height:25px;border:1px solid #ddd;font-size:7.5px;color:#666;padding:6px 5px">Enter your email address</div>
    <span class="abs cond" style="left:117px;top:109px;width:83px;height:24px;background:var(--red);color:#fff;font-size:13px;font-weight:700;display:flex;align-items:center;justify-content:center;letter-spacing:.6px">SUBSCRIBE</span>
    <div class="abs cond" style="left:11px;top:152px;font-size:10px;color:#444;letter-spacing:.5px">FOLLOW US ON</div>
    <div class="abs social" style="left:103px;top:149px" aria-label="Social networks">
      <span style="background:#3b5ea8"></span><span style="background:#33b1e6"></span><span style="background:#1a86c0"></span><span style="background:#d8442f"></span><span style="background:#d8302a"></span>
    </div>
  </div>
</aside>

<section class="abs promo">
  <div class="abs cond" style="left:13px;top:6px;font-size:27px;font-weight:700;color:#1f3a7a;white-space:nowrap">Get Ready to <span style="color:#fff">Quake Ready.</span></div>
  <div class="abs cond" style="left:15px;top:38px;font-size:14px;font-weight:700;color:#fff">November 13, 2008</div>
  <div class="abs cond" style="left:179px;top:42px;font-size:10px;font-weight:700;color:#fff">Register Now at www.quakeready.org</div>
  <div class="promo-side">
    <div class="abs cond" style="left:0;width:100%;top:5px;text-align:center;font-size:6px;font-weight:700;color:#fff;line-height:7px">The Great<br>Coastal Quake Ready</div>
    <div class="abs cond" style="left:0;width:100%;top:22px;text-align:center;font-size:20px;font-weight:700;color:#fff;line-height:20px">Quake<br>Ready</div>
  </div>
</section>

<footer class="abs footer">
  <div><b>Job Vacancies</b> - Beauty: Aux Hairdresser | Aux Escovista | Hairdresser | epilator | Manicure | Makeup | Eyebrow Designer</div>
  <div><b>Job Vacancies</b> - Health and Wellness: Esthetician | Massage Therapist | Podiatrist | Physiotherapist | Nurse</div>
  <div><b>Job Vacancies</b> - Sales and Admin: Front | Sale Cosmetics | Auxiliary Cleaning | Management</div>
</footer>
<div class="abs copy">Copyright 2013 @ Lumarinovo Beauty - Your Community for Professionals and Companies Beauty, Aesthetics and Wellness</div>

</body>
</html>
```